Fresh, modern, fun business card for pediatric dental practice

Need a business card for fresh, modern, fun pediatric dental practice

Clean look that matches our website's font and colors

We prefer the look of curved corners on business cards

Target Market(s)

parents (mothers) of young children, professionals, mid-high class

Industry/Entity Type

Dental

Contact Information for Business Card

Maplebrook Pediatric Dentistry
482 Quarry Lane
Suite 517
Fernvale, OR 97999
503.555.0193
www.maplebrookkidsdental.example

Mei-Ran Tsai, DMD
Corinne Walbeck, DMD
(we are working on our email address, but we would like that on the card as well)

Font styles to use
Sans Serif

Requirements
Must have
• All info; we would also like to make cards for individual staff members
• colors from our website and color palatte, attatched
• use same font and design as website for branding
Nice to have
• clean, simple card that has a pop of color
• we would like to see a few designs with our tag line "where smiles get brighter"
• we are not sure if we want to have it on there or not
• we would like to see a few designs incorporating the ribbon graphic on our website where the word WELCOME is

```html
<!DOCTYPE html>
<html lang="en">
<head>
<meta charset="utf-8">
<title>Maplebrook Pediatric Dentistry – Business Card</title>
<link rel="stylesheet" href="https://fonts.googleapis.com/css2?family=Ubuntu:wght@500;700&family=Montserrat:wght@400;700&display=swap">
<style>
  :root {
    --backdrop: #262626;
    --card: #141414;
    --sun: #fdb913;
    --sun-faint: #3b2f12;
    --ink-light: #e6e6e6;
    --radius: 22px;
  }
  * { margin: 0; padding: 0; box-sizing: border-box; }
  html, body {
    width: 1200px; height: 852px; overflow: hidden;
    background: var(--backdrop);
  }
  .sheet { position: relative; width: 1200px; height: 852px; }
  .card {
    position: absolute; left: 290px; width: 620px; height: 354px;
    background: var(--card); border-radius: var(--radius);
    overflow: hidden;
  }
  .card--back { top: 52px; }
  .card--front { top: 446px; }

  .wordmark {
    position: absolute;
    font-family: "Ubuntu", sans-serif; font-weight: 700;
    color: var(--sun); line-height: 1.05; letter-spacing: 0.5px;
  }
  .wordmark__line { display: block; }
  .wordmark__dot {
    display: block; border-radius: 50%; background: var(--sun);
    margin-bottom: 8px;
  }

  .card--back .wordmark { left: 40px; bottom: 40px; font-size: 30px; }
  .card--back .wordmark__dot { width: 26px; height: 26px; }
  .card--back .sun-mark {
    position: absolute; right: 95px; top: 50px;
    width: 170px; height: 170px; border-radius: 50%;
    background: var(--sun-faint);
  }

  .card--front .wordmark { left: 40px; top: 40px; font-size: 30px; }
  .card--front .sun-mark {
    position: absolute; right: 70px; top: 78px;
    width: 180px; height: 180px; border-radius: 50%;
    background: var(--sun);
  }

  .person {
    position: absolute; left: 40px; top: 150px;
    font-family: "Montserrat", sans-serif;
  }
  .person__name {
    font-weight: 700; font-size: 20px; color: var(--sun);
    letter-spacing: 0.3px; text-transform: uppercase;
  }
  .person__title { font-size: 13px; color: var(--ink-light); margin-top: 2px; }

  .address {
    position: absolute; left: 58px; top: 210px;
    font-family: "Montserrat", sans-serif; font-size: 13px;
    color: var(--ink-light); line-height: 1.45; font-style: normal;
  }
  .contacts {
    position: absolute; left: 40px; top: 262px; list-style: none;
    font-family: "Montserrat", sans-serif; font-size: 13px;
    color: var(--ink-light); line-height: 1.45;
  }
  .contacts li { display: flex; align-items: center; gap: 8px; }
  .contacts svg { width: 10px; height: 10px; flex: none; }
</style>
</head>
<body>
<main class="sheet">

  <section class="card card--back" aria-label="Card back">
    <div class="sun-mark" aria-hidden="true"></div>
    <div class="wordmark">
      <span class="wordmark__dot" aria-hidden="true"></span>
      <span class="wordmark__line">Maplebrook</span>
      <span class="wordmark__line">Pediatric Dentistry</span>
    </div>
  </section>

  <section class="card card--front" aria-label="Card front">
    <div class="wordmark">
      <span class="wordmark__line">Maplebrook</span>
      <span class="wordmark__line">Pediatric Dentistry</span>
    </div>
    <div class="sun-mark" aria-hidden="true"></div>

    <div class="person">
      <p class="person__name">Corinne Walbeck</p>
      <p class="person__title">DMD</p>
    </div>

    <address class="address">
      482 Quarry Lane<br>
      Suite 517 Fernvale, OR 97999
    </address>

    <ul class="contacts">
      <li>
        <svg viewBox="0 0 10 10" aria-hidden="true"><path d="M2 0.5 L3.8 2.6 L2.9 3.7 Q4.2 6 6.3 7.1 L7.4 6.2 L9.5 8 L8.3 9.5 Q3.5 8.5 0.5 1.7 Z" fill="#fdb913"/></svg>
        503.555.0193
      </li>
      <li>
        <svg viewBox="0 0 10 10" aria-hidden="true"><rect x="0.7" y="2" width="8.6" height="6" fill="none" stroke="#fdb913" stroke-width="1.2"/><path d="M0.7 2 L5 5.5 L9.3 2" fill="none" stroke="#fdb913" stroke-width="1.2"/></svg>
        hello@maplebrookkidsdental.example
      </li>
      <li>
        <svg viewBox="0 0 10 10" aria-hidden="true"><circle cx="5" cy="5" r="4.3" fill="none" stroke="#fdb913" stroke-width="1.1"/><ellipse cx="5" cy="5" rx="1.8" ry="4.3" fill="none" stroke="#fdb913" stroke-width="1"/><path d="M0.7 5 H9.3" stroke="#fdb913" stroke-width="1"/></svg>
        www.maplebrookkidsdental.example
      </li>
    </ul>
  </section>

</main>
</body>
</html>
```